The design should look similar to the uploaded example to accommodate the information needed for a business card template. I would like to see the colors orange and charcoal grey incorporated along with the logo.The following should be on the back of the card SPECIALIZING IN NEW AND USED TIRES & WHEELS FOR:- Loaders- Skid Steers- Telehandlers- Boom Lifts- Forklifs and moreELIMINATING DOWNTIMEWheel Exchange Program for New & Used Foam Filled and Solid Rubber TiresSPECIALTY SERVICES- Foam Filling Tires- Largest Tire Press in SE- ONSITE Forklift Tire Press- Boom Truck Services - Rubber Tracks

Target Market(s)

New and Existing Customers

Industry/Entity Type

Business

Contact Information for Business Card

NAMEHEAVY DUTY TIRE, LLC8470 Belvedere RoadWest Palm Beach, FL 33411P: 844-HD-TIRESF: 561-431-6469C:E: W: WWW.GRANITERIMSUPPLY-EXAMPLE.COM

Font styles to use
Sans Serif

Colors
f37122
333333

Requirements
Must have
• The logo and the information indicated for the backside of the card
Nice to have
• Keep the orange and charcoal grey colors

```html
<!DOCTYPE html>
<html lang="en">
<head>
<meta charset="utf-8">
<title>Granite Rim Supply – Business Card</title>
<link href="https://fonts.googleapis.com/css2?family=Open+Sans:wght@400;600;700&display=swap" rel="stylesheet">
<style>
  :root {
    --orange: #f37122;
    --charcoal: #333333;
    --card: #141414;
    --ink: #f2f2f2;
    --divider: #262626;
    --backdrop: #3a3633;
  }
  * { box-sizing: border-box; margin: 0; padding: 0; }
  html, body { width: 1200px; height: 900px; overflow: hidden; }
  body {
    background: var(--backdrop);
    font-family: "Open Sans", sans-serif;
    color: var(--ink);
    display: flex;
    align-items: center;
    justify-content: center;
    gap: 40px;
  }
  .card {
    width: 540px;
    height: 309px;
    background: var(--card);
    border-radius: 4px;
    box-shadow: 0 10px 30px rgba(0,0,0,.45);
    position: relative;
    overflow: hidden;
  }
  /* Front */
  .card-front { display: flex; }
  .brand {
    width: 230px;
    display: flex;
    flex-direction: column;
    align-items: center;
    justify-content: center;
    gap: 14px;
  }
  .brand-mark {
    width: 70px; height: 70px;
    border-radius: 50%;
    background: var(--charcoal);
  }
  .brand-name {
    color: var(--orange);
    font-weight: 700;
    font-size: 22px;
    letter-spacing: 1px;
    text-align: center;
    line-height: 1.15;
  }
  .details {
    flex: 1;
    border-left: 1px solid var(--divider);
    padding: 54px 16px 0 24px;
  }
  .person-name { color: var(--orange); font-size: 19px; font-weight: 600; }
  .company { color: var(--orange); font-size: 14px; font-weight: 600; margin-top: 4px; }
  .address { font-size: 13px; line-height: 1.45; margin-top: 6px; }
  .contacts { list-style: none; margin-top: 14px; font-size: 13px; line-height: 1.55; }
  .contacts li { display: flex; align-items: center; gap: 9px; white-space: nowrap; }
  .contacts svg { width: 11px; height: 11px; fill: var(--orange); flex: none; }
  /* Back */
  .card-back {
    display: flex;
    flex-direction: column;
    align-items: center;
    justify-content: center;
    text-align: center;
    padding: 0 26px;
  }
  .heading { color: var(--orange); font-weight: 600; }
  .heading-lg { font-size: 15px; }
  .heading-sm { font-size: 11px; margin-top: 16px; }
  .heading-md { font-size: 16px; margin-top: 16px; }
  .line { font-size: 12.5px; line-height: 1.5; }
  .bullet {
    display: inline-block; width: 6px; height: 6px; border-radius: 50%;
    background: var(--orange); margin: 0 7px; vertical-align: middle;
  }
  .list { margin-top: 6px; }
</style>
</head>
<body>
  <section class="card card-front">
    <div class="brand">
      <span class="brand-mark"></span>
      <span class="brand-name">GRANITE RIM</span>
    </div>
    <div class="details">
      <h1 class="person-name">Daniel Reyes</h1>
      <p class="company">GRANITE RIM SUPPLY, LLC</p>
      <p class="address">5126 Marston Lane<br>Lakeview Harbor, FL 33987</p>
      <ul class="contacts">
        <li><svg viewBox="0 0 12 12"><path d="M2 1l2.5 0 1 3-1.5 1a7 7 0 0 0 3 3l1-1.5 3 1V10a1 1 0 0 1-1 1A9 9 0 0 1 1 2a1 1 0 0 1 1-1z"/></svg>844-GR-WHEEL</li>
        <li><svg viewBox="0 0 12 12"><rect x="1" y="4" width="10" height="7" rx="1"/><rect x="3" y="1" width="6" height="3"/></svg>561-278-9053</li>
        <li><svg viewBox="0 0 12 12"><rect x="3" y="0.5" width="6" height="11" rx="1"/></svg>123-456-7890</li>
        <li><svg viewBox="0 0 12 12"><rect x="0.5" y="2" width="11" height="8" rx="1"/></svg>info@graniterim-example.com</li>
        <li><svg viewBox="0 0 12 12"><circle cx="6" cy="6" r="5.5"/></svg>www.graniterimsupply-example.com</li>
      </ul>
    </div>
  </section>

  <section class="card card-back">
    <h2 class="heading heading-lg">SPECIALIZING IN NEW AND USED TIRES &amp; WHEELS FOR</h2>
    <div class="list">
      <p class="line">Loaders<span class="bullet"></span>Skid Steers<span class="bullet"></span>Telehandlers<span class="bullet"></span>Boom Lifts</p>
      <p class="line">Forklifs and more</p>
    </div>
    <h3 class="heading heading-sm">ELIMINATING DOWNTIME</h3>
    <p class="line">Wheel Exchange Program for New &amp; Used Foam<br>Filled and Solid Rubber Tires</p>
    <h3 class="heading heading-md">SPECIALTY SERVICES</h3>
    <div class="list">
      <p class="line">Foam Filling Tires<span class="bullet"></span>Largest Tire Press in SE</p>
      <p class="line">ONSITE Forklift Tire Press<span class="bullet"></span>Boom Truck Services<span class="bullet"></span>Rubber Tracks</p>
    </div>
  </section>
</body>
</html>
```